Hello my Name is Elias Moreno. I buy and sell vintage comic books, you can refer to my instragram page qpkz.comics to get ideas and inspiration. For the front of the card I would like my company logo QPKZ Comics with a yellow and black background with the bat signal or bat emblem like on my IG page and with my info Elias Moreno as the Owner and address/ phone number, PO Box 617283, Miami, FL 33827, 305-482-6170 and that I buy and sell comics & collectables . Also feel free to be open to other ideas if you want. Im not stuck on one design. For the back of the card I would like for it to say follow me on Instagram QPKZ.Comics with the ig emblem. Also would like the card to be vertical if possible. Thanks

```html
<!DOCTYPE html>
<html lang="en">
<head>
<meta charset="utf-8">
<title>QPKZ Comics – Business Cards</title>
<link rel="stylesheet" href="https://fonts.googleapis.com/css2?family=Open+Sans:wght@400;600;700&family=Orbitron:wght@700;900&display=swap">
<style>
  :root {
    --stage: #1b1c1e;
    --card-white: #ffffff;
    --brand-yellow: #f8c51a;
    --ink: #111111;
    --muted: #6b6b6b;
  }
  * { margin: 0; padding: 0; box-sizing: border-box; }
  html, body { width: 1200px; height: 987px; overflow: hidden; }
  body { background: var(--stage); position: relative; font-family: "Open Sans", sans-serif; }

  .card {
    position: absolute;
    top: 196px;
    width: 340px;
    height: 595px;
  }
  .card--front { left: 215px; background: var(--card-white); }
  .card--back { left: 645px; background: var(--brand-yellow); }

  /* Front */
  .logo-tile {
    position: absolute;
    left: 38px; top: 62px;
    width: 170px; height: 170px;
    background: var(--brand-yellow);
    display: flex; flex-direction: column; align-items: center; justify-content: center;
    font-family: "Orbitron", sans-serif; font-weight: 900; color: var(--ink);
    line-height: 1.05;
  }
  .logo-tile .wordmark-main { font-size: 40px; }
  .logo-tile .wordmark-sub { font-size: 16px; letter-spacing: 1px; margin-top: 4px; }

  .contact {
    position: absolute;
    left: 38px; bottom: 52px;
    color: var(--muted);
    font-size: 14px;
    line-height: 1.45;
  }
  .contact .name { color: var(--brand-yellow); font-weight: 700; font-size: 20px; line-height: 1.2; }
  .contact .role { color: var(--ink); font-size: 14px; margin-bottom: 14px; }
  .contact .address { margin-bottom: 10px; }
  .contact .line { display: flex; align-items: center; gap: 8px; }
  .contact svg { width: 12px; height: 12px; fill: var(--brand-yellow); flex: none; }

  /* Back */
  .brand-block {
    position: absolute;
    left: 0; right: 0; top: 150px;
    text-align: center;
    font-family: "Orbitron", sans-serif; font-weight: 900; color: var(--ink);
    line-height: 1;
  }
  .brand-block .wordmark-main { font-size: 72px; }
  .brand-block .wordmark-sub { font-size: 28px; letter-spacing: 2px; margin-top: 10px; }

  .social {
    position: absolute;
    left: 0; right: 0; top: 420px;
    display: flex; justify-content: center; align-items: center; gap: 10px;
    font-size: 19px; color: var(--ink);
  }
  .social .marker { width: 22px; height: 22px; border: 2.5px solid var(--ink); flex: none; }

  .tagline {
    position: absolute;
    left: 0; right: 0; top: 478px;
    text-align: center;
    font-family: "Orbitron", sans-serif; font-weight: 900;
    font-size: 16px; letter-spacing: 1px; line-height: 1.35;
    color: var(--ink);
  }
</style>
</head>
<body>
  <section class="card card--front">
    <div class="logo-tile">
      <span class="wordmark-main">QPKZ</span>
      <span class="wordmark-sub">COMICS</span>
    </div>
    <div class="contact">
      <p class="name">ELIAS MORENO</p>
      <p class="role">OWNER</p>
      <p class="address">PO Box 617283<br>Miami, FL 33827</p>
      <p class="line">
        <svg viewBox="0 0 24 24" aria-hidden="true"><path d="M6.6 10.8a15.1 15.1 0 0 0 6.6 6.6l2.2-2.2c.3-.3.7-.4 1-.2 1.1.4 2.3.6 3.6.6.6 0 1 .4 1 1V20c0 .6-.4 1-1 1C10.6 21 3 13.4 3 4c0-.6.4-1 1-1h3.5c.6 0 1 .4 1 1 0 1.3.2 2.5.6 3.6.1.3 0 .7-.2 1z"/></svg>
        305-482-6170
      </p>
      <p class="line">
        <svg viewBox="0 0 24 24" aria-hidden="true"><path d="M2 5h20v14H2z"/><path d="M2 5l10 8 10-8v2l-10 8L2 7z" fill="#fff"/></svg>
        hello@qpkzmail.com
      </p>
      <p class="line">
        <svg viewBox="0 0 24 24" aria-hidden="true"><circle cx="12" cy="12" r="10"/></svg>
        www.qpkzstore.com
      </p>
    </div>
  </section>

  <section class="card card--back">
    <div class="brand-block">
      <div class="wordmark-main">QPKZ</div>
      <div class="wordmark-sub">COMICS</div>
    </div>
    <p class="social"><span class="marker"></span>QPKZ.Comics</p>
    <p class="tagline">BUY &amp; SELL COMICS<br>&amp; COLLECTABLES</p>
  </section>
</body>
</html>
```